New eyelid plastic surgery office needs a business card design-Eyelid Care Partners of the Brenton

I recently used PixelForge for my logo design and was very pleased with creativity and results. It was a difficult decision for me. Now I would like to create a business card based on this logo, which I will attach.

The text should be easily legible as some of my patients have difficulty seeing, but I would like a subtle, sophisticated artistry also evident to make the card memorable. Would like the card based on a similar color scheme as the logo but the inverse or other complementary colors may prove interesting
Updates

A good question was asked...my concern about my visually impaired patients was really my desire to avoid italicized or calligraphic type fonts that may be hard to read. Standard font size for a business card would be fine. Thanks!

Thank you so much for the great work so far. I wanted to give you my particular contact information to see if that would change the look of the cards. Martin Delacourt, MD Address: 2718 Harborview Lane, Suite 206 Wilmington, NC 28517 Phone: 910-555-0193 Fax: 910-555-0194 Website: www.brentonlidstudio.example Please delete the email slot from the card. Thanks so much!

Industry/Entity Type

Plastic

```html
<!DOCTYPE html>
<html lang="en">
<head>
<meta charset="utf-8">
<title>Eyelid Care Partners of the Brenton – Business Card</title>
<link rel="stylesheet" href="https://fonts.googleapis.com/css2?family=Didact+Gothic&display=swap">
<style>
  :root {
    --canvas-bg: #e4e4e2;
    --card-white: #f4f4f4;
    --card-black: #0a0a0a;
    --brand-blue: #2f4f9e;
    --text-dark: #2b2b2b;
    --text-mid: #4a4a4a;
    --edge-grey: #dcdcdc;
  }
  * { box-sizing: border-box; margin: 0; padding: 0; }
  html, body { width: 1200px; height: 900px; overflow: hidden; }
  body {
    background: var(--canvas-bg);
    font-family: "Didact Gothic", "Century Gothic", sans-serif;
    position: relative;
  }
  .card {
    position: absolute;
    left: 250px;
    width: 700px;
    height: 400px;
    overflow: hidden;
    box-shadow: 0 4px 14px rgba(0,0,0,0.18);
  }
  .card--front { top: 30px; background: var(--card-white); }
  .card--back { top: 470px; background: var(--card-black); }

  .card__shape { position: absolute; inset: 0; }

  .brand-name {
    position: absolute;
    color: var(--brand-blue);
    font-weight: 400;
    text-align: center;
    line-height: 1.05;
    letter-spacing: 0.02em;
  }
  .brand-name__main { display: block; font-size: 34px; }
  .brand-name__sub { display: block; font-size: 16px; letter-spacing: 0.12em; margin-top: 6px; }
  .card--front .brand-name { left: 250px; top: 56px; width: 340px; }
  .card--back .brand-name { left: 0; right: 0; top: 150px; }
  .card--back .brand-name__main { font-size: 46px; }
  .card--back .brand-name__sub { font-size: 20px; }

  .person { position: absolute; left: 48px; top: 150px; }
  .person__name {
    font-size: 21px;
    color: var(--text-dark);
    letter-spacing: 0.14em;
    font-weight: 400;
    -webkit-text-stroke: 0.5px var(--text-dark);
  }
  .person__title {
    font-size: 12px;
    color: var(--brand-blue);
    letter-spacing: 0.16em;
    margin-top: 8px;
  }

  .contact { position: absolute; left: 340px; top: 190px; color: var(--text-mid); }
  .contact__locations { font-size: 14px; letter-spacing: 0.14em; margin-bottom: 14px; padding-left: 30px; }
  .contact__list { list-style: none; }
  .contact__item {
    display: flex; align-items: center; gap: 14px;
    font-size: 15px; letter-spacing: 0.14em; margin-bottom: 9px;
  }
  .contact__icon { width: 16px; height: 16px; flex: none; }
</style>
</head>
<body>

<section class="card card--front" aria-label="Business card front">
  <svg class="card__shape" viewBox="0 0 700 400" aria-hidden="true">
    <path d="M0 0 H10 V300 Q40 345 140 362 H700 V400 H0 Z" fill="var(--edge-grey)"/>
    <path d="M0 340 Q40 372 150 376 H700 V400 H0 Z" fill="var(--brand-blue)"/>
  </svg>

  <div class="brand-name">
    <span class="brand-name__main">Eyelid Care Partners</span>
    <span class="brand-name__sub">OF THE BRENTON</span>
  </div>

  <div class="person">
    <h1 class="person__name">Delia Marsh Keane</h1>
    <p class="person__title">Director of Operations</p>
  </div>

  <div class="contact">
    <p class="contact__locations">Washington DC | New York</p>
    <ul class="contact__list">
      <li class="contact__item">
        <svg class="contact__icon" viewBox="0 0 16 16" aria-hidden="true"><path d="M3 2 L6 2 L7 5 L5.5 6.5 Q7 9.5 9.5 10.5 L11 9 L14 10 L14 13 Q8 14 3 8 Q2 5 3 2 Z" fill="var(--brand-blue)"/></svg>
        <span>301-555-0147</span>
      </li>
      <li class="contact__item">
        <svg class="contact__icon" viewBox="0 0 16 16" aria-hidden="true"><rect x="1.5" y="3.5" width="13" height="9" fill="none" stroke="var(--brand-blue)" stroke-width="1.5"/><path d="M1.5 3.5 L8 9 L14.5 3.5" fill="none" stroke="var(--brand-blue)" stroke-width="1.5"/></svg>
        <span>dmkeane@eyelidcare.example</span>
      </li>
      <li class="contact__item">
        <svg class="contact__icon" viewBox="0 0 16 16" aria-hidden="true"><circle cx="8" cy="8" r="6.3" fill="none" stroke="var(--brand-blue)" stroke-width="1.5"/><ellipse cx="8" cy="8" rx="2.6" ry="6.3" fill="none" stroke="var(--brand-blue)" stroke-width="1.2"/><path d="M1.7 8 H14.3" stroke="var(--brand-blue)" stroke-width="1.2"/></svg>
        <span>www.eyelidcare.example</span>
      </li>
    </ul>
  </div>
</section>

<section class="card card--back" aria-label="Business card back">
  <div class="brand-name">
    <span class="brand-name__main">Eyelid Care Partners</span>
    <span class="brand-name__sub">OF THE BRENTON</span>
  </div>
</section>

</body>
</html>
```